SavannaPlate Web Page Templates

I need two templates designed for a wholesale food/catering business, one template for the home page and the other for detail pages. The overall template should be a simple, clean and clear design. I have provided the existing logo to which the templates should directly relate.
SavannaPlate supplies food based upon traditional Ghanian recipes to a number of stores across Canberra. In addition, SavannaPlate offers catering for public and private functions across the Canberra region.
The colours in the logo represent the national colours of Ghana (yellow, green, red and black) and the website content will also include traditional Ghanian Kente patterns which will add further colour elements to the site. On this basis, the template design needs to be fairly sparse so as not to compete with the colourful content of the website detail pages.
There is no requirement for specific pages to be designed, as these will be handled in the CMS implementation.
The information provided in the Word document is only designed to provide a sense of the intended content of the website, not as a requirement for specific pages to be produced.

Target Market(s)

Retail/Wholesale food

Number of Pages Required

2 page

Font styles to use
Serif

Colors

Designer to choose colors to be used in the design.

Requirements
Must have
• Template must accommodate a responsive design
• The logo provided will form the cornerstone of the design
Nice to have
• There
Should not have
• Please do not solicit for extra work or for alternative logo design.

```html
<!DOCTYPE html>
<html lang="en">
<head>
<meta charset="utf-8">
<title>SavannaPlate – Home</title>
<link href="https://fonts.googleapis.com/css2?family=Questrial&family=Source+Sans+3:wght@400;600&family=Lato:wght@400&display=swap" rel="stylesheet">
<style>
:root{
  --orange:#f08a1e;
  --orange-dark:#e27a10;
  --ink:#1e1e1e;
  --grey:#666;
  --white:#fff;
  --black:#000;
}
*{margin:0;padding:0;box-sizing:border-box}
html,body{width:1200px;height:3707px;overflow:hidden;background:var(--white)}
body{position:relative;font-family:'Source Sans 3',sans-serif;color:var(--ink)}
.abs{position:absolute}
.heading{font-family:'Questrial',sans-serif;font-weight:400}

/* header */
.site-header{left:0;top:0;width:1200px;height:103px}
.brand{left:95px;top:22px;display:flex;align-items:center;gap:12px}
.brand-mark{width:34px;height:34px;border-radius:50%;background:var(--orange)}
.brand-name{font-family:'Questrial',sans-serif;font-size:44px;color:var(--ink)}
.contact-item{top:22px;display:flex;align-items:center;gap:16px;font-size:22px}
.contact-icon{width:60px;height:60px;border:2px solid var(--orange);border-radius:50%;display:flex;align-items:center;justify-content:center}
.phone-item{left:557px;font-weight:600}
.mail-item{left:802px;color:#444}

.main-nav{left:0;top:103px;width:1200px;height:48px;background:var(--orange)}
.main-nav a{position:absolute;top:12px;color:var(--white);text-decoration:none;font-size:18px}
.main-nav a.active{color:#ffe2c2}

/* hero */
.hero{left:0;top:151px;width:1200px;height:604px;background:radial-gradient(ellipse at 40% 55%,#d9cbb8 0%,#8a7562 35%,#3b3129 75%,#1e1915 100%)}
.hero-title{left:0;top:285px;width:1200px;text-align:center;font-family:'Questrial',sans-serif;font-size:84px;color:var(--white)}
.wave{left:0;width:1200px;height:40px}

/* intro */
.intro{left:150px;width:900px;text-align:center}
.intro h1{font-size:42px;margin-bottom:22px}
.intro p{font-size:15px;line-height:30px;color:#444}
.intro .cta{margin-top:22px;font-size:20px;color:var(--orange)}

/* partners */
.partners{left:0;top:1173px;width:1200px;height:979px;background:var(--orange)}
.partners h2{position:absolute;left:0;top:88px;width:1200px;text-align:center;color:var(--white);font-size:42px}
.stockist{position:absolute;width:311px}
.stockist-photo{width:311px;height:236px;border-radius:22px;position:relative}
.stockist-badge{position:absolute;left:10px;top:10px;width:62px;height:62px;border-radius:50%;background:var(--white)}
.stockist-name{text-align:center;color:var(--white);font-size:25px;margin-top:16px}
.btn-outline{position:absolute;left:511px;top:827px;width:179px;height:58px;border:2px solid var(--white);border-radius:30px;color:var(--white);font-size:21px;display:flex;align-items:center;justify-content:center}

/* dishes */
.section-title{left:0;width:1200px;text-align:center;font-size:42px}
.dish{position:absolute;width:496px;height:243px;border-radius:24px;background:var(--white);box-shadow:0 0 0 3px #eee,0 2px 8px rgba(0,0,0,.12);overflow:hidden}
.dish-photo{position:absolute;top:6px;width:232px;height:231px;border-radius:20px}
.dish-body{position:absolute;top:28px;width:240px}
.dish-body h3{font-size:30px;line-height:35px;margin-bottom:12px}
.dish-body p{font-family:'Lato',sans-serif;font-size:17px;line-height:30px;color:var(--grey)}
.dish-body a{display:inline-block;margin-top:14px;font-family:'Lato',sans-serif;font-size:17px;color:var(--orange)}
.btn-fill{left:511px;top:2870px;width:179px;height:58px;border-radius:30px;background:var(--orange);color:var(--white);font-size:21px;display:flex;align-items:center;justify-content:center}

/* gallery */
.gallery-item{top:3084px;width:248px;height:221px}
.gallery-caption{position:absolute;left:0;bottom:0;width:100%;height:58px;background:rgba(0,0,0,.55);color:var(--white);font-size:18px;display:flex;align-items:center;justify-content:center}

/* footer */
.site-footer{left:0;top:3410px;width:1200px;height:297px;background:var(--black);color:var(--white)}
.social{position:absolute;top:86px;width:52px;height:52px;border:2px solid var(--orange);border-radius:50%}
.footer-contacts{position:absolute;top:175px;left:0;width:1200px;display:flex;justify-content:center;align-items:center;gap:12px;font-size:14px}
.footer-nav{position:absolute;top:213px;left:0;width:1200px;display:flex;justify-content:center;gap:33px;font-size:14px}
.copyright{position:absolute;top:250px;left:0;width:1200px;text-align:center;font-size:13px}
</style>
</head>
<body>

<svg width="0" height="0" style="position:absolute">
  <defs>
    <pattern id="scallopDown" width="66" height="40" patternUnits="userSpaceOnUse">
      <path d="M0 20 Q16.5 6 33 20 T66 20 V40 H0Z" fill="#fff"/>
      <path d="M0 20 Q16.5 6 33 20 T66 20" fill="none" stroke="#f08a1e" stroke-width="4"/>
    </pattern>
    <pattern id="scallopUp" width="66" height="40" patternUnits="userSpaceOnUse">
      <path d="M0 20 Q16.5 34 33 20 T66 20 V0 H0Z" fill="#fff"/>
      <path d="M0 20 Q16.5 34 33 20 T66 20" fill="none" stroke="#f08a1e" stroke-width="4"/>
    </pattern>
  </defs>
</svg>

<header class="abs site-header">
  <div class="abs brand">
    <span class="brand-mark"></span>
    <span class="brand-name">SavannaPlate</span>
  </div>
  <div class="abs contact-item phone-item">
    <span class="contact-icon"><svg width="22" height="22" viewBox="0 0 24 24"><path d="M6.6 10.8c1.4 2.8 3.8 5.1 6.6 6.6l2.2-2.2c.3-.3.7-.4 1-.2 1.1.4 2.3.6 3.6.6.6 0 1 .4 1 1V20c0 .6-.4 1-1 1C10.6 21 3 13.4 3 4c0-.6.4-1 1-1h3.5c.6 0 1 .4 1 1 0 1.3.2 2.5.6 3.6.1.3 0 .7-.2 1z" fill="#f08a1e"/></svg></span>
    <span>02 6100 4827</span>
  </div>
  <div class="abs contact-item mail-item">
    <span class="contact-icon"><svg width="24" height="20" viewBox="0 0 24 18"><rect x="1" y="1" width="22" height="16" rx="2" fill="#f08a1e"/><path d="M2 3l10 7 10-7" fill="none" stroke="#fff" stroke-width="2"/></svg></span>
    <span>hello@savannaplate.example</span>
  </div>
</header>

<nav class="abs main-nav">
  <a class="active" style="left:155px">Home</a>
  <a style="left:249px">About Us</a>
  <a style="left:367px">Services</a>
  <a style="left:479px">We Offer</a>
  <a style="left:593px">Our Dishes</a>
  <a style="left:725px">Our Partners</a>
  <a style="left:873px">Blog</a>
  <a style="left:953px">Contact Us</a>
</nav>

<section class="abs hero" role="img" aria-label="Chef's hands plating a garnished dish"></section>
<div class="abs hero-title">SavannaPlate</div>
<svg class="abs wave" style="top:720px" width="1200" height="40"><rect width="1200" height="40" fill="url(#scallopDown)"/></svg>

<section class="abs intro" style="top:842px">
  <h1 class="heading">SavannaPlate commenced in 2004</h1>
  <p>Coming from Ghana and with a passion for cooking I realized, through school P&amp;C fundraising, that as well as enjoying my dishes, people wanted to learn more about Ghanaian food. So I started introducing pre-packaged meals at farmersmarkets and food festivals to showcase Ghanaian food far and wide. They took off! People relished the exotic flavours. So why don’t you give it a go?</p>
  <p class="cta">Have a taste! Enjoy!!</p>
</section>

<section class="abs partners">
  <h2 class="heading">Our beautiful freshly made food</h2>
  <div class="stockist" style="left:89px;top:176px"><div class="stockist-photo" role="img" aria-label="Broccoli and cheese bake" style="background:linear-gradient(135deg,#e8e6df,#c9c18a 50%,#7f9c4a)"><span class="stockist-badge"></span></div><div class="stockist-name">Baobab Market Curtin</div></div>
  <div class="stockist" style="left:445px;top:176px"><div class="stockist-photo" role="img" aria-label="Bowl of bean chilli with crackers" style="background:linear-gradient(135deg,#8fa0a0,#a3402a 55%,#5d6b6b)"><span class="stockist-badge"></span></div><div class="stockist-name">Ainslie Corner Grocer</div></div>
  <div class="stockist" style="left:800px;top:176px"><div class="stockist-photo" role="img" aria-label="Cheesy pasta bake in a white dish" style="background:linear-gradient(135deg,#6f8fa8,#e0b443 55%,#8aa4b8)"><span class="stockist-badge"></span></div><div class="stockist-name">Deakin Fresh Foods</div></div>
  <div class="stockist" style="left:89px;top:499px"><div class="stockist-photo" role="img" aria-label="Meatballs in tomato sauce" style="background:linear-gradient(135deg,#eeeeec,#d6602a 55%,#c9c9c4)"><span class="stockist-badge"></span></div><div class="stockist-name">Harvest Table, Braddon</div></div>
  <div class="stockist" style="left:445px;top:499px"><div class="stockist-photo" role="img" aria-label="Rice and bean salad on a blue plate" style="background:linear-gradient(135deg,#1f4f8a,#c9b48f 50%,#1a3e70)"><span class="stockist-badge"></span></div><div class="stockist-name">Green Basket, Mawson</div></div>
  <div class="stockist" style="left:800px;top:499px"><div class="stockist-photo" role="img" aria-label="Sliced beef in a cast iron pan" style="background:linear-gradient(135deg,#6b5a4a,#7a2a1c 50%,#2a2220)"><span class="stockist-badge"></span></div><div class="stockist-name">Lyneham Pantry</div></div>
  <div class="btn-outline">View All</div>
</section>

<h2 class="abs section-title heading" style="top:2240px">We offer special dishes</h2>

<article class="dish" style="left:89px;top:2318px">
  <div class="dish-photo" role="img" aria-label="Jollof rice with chicken" style="left:6px;background:linear-gradient(135deg,#c6351c,#e0622e 50%,#7a1f12)"></div>
  <div class="dish-body" style="left:254px"><h3 class="heading">Jollof rice.</h3><p>Lorem ipsum dolor sit amet, consectetur adipiscing elit, sed do eiusmod tempor</p><a>View Details</a></div>
</article>
<article class="dish" style="left:615px;top:2318px">
  <div class="dish-photo" role="img" aria-label="Gari fortor stew in a bowl" style="left:6px;background:linear-gradient(135deg,#d8cfc4,#a8321c 55%,#e8e2da)"></div>
  <div class="dish-body" style="left:254px"><h3 class="heading">Gari Fortor.</h3><p>Lorem ipsum dolor sit amet, consectetur adipiscing elit, sed do eiusmod tempor</p><a>View Details</a></div>
</article>
<article class="dish" style="left:89px;top:2596px">
  <div class="dish-photo" role="img" aria-label="Ghanaian chilli sauce in a glass" style="left:258px;background:linear-gradient(135deg,#5a4536,#d9291c 50%,#4a3a2e)"></div>
  <div class="dish-body" style="left:15px"><h3 class="heading">Ghanaian chilli sauce.</h3><p>Lorem ipsum dolor sit amet, consectetur adipiscing</p><a>View Details</a></div>
</article>
<article class="dish" style="left:615px;top:2596px">
  <div class="dish-photo" role="img" aria-label="Coconut sweets on a white plate" style="left:258px;background:linear-gradient(135deg,#5b5048,#f2efe8 50%,#4a4038)"></div>
  <div class="dish-body" style="left:15px"><h3 class="heading">Coconut sweet.</h3><p>Lorem ipsum dolor sit amet, consectetur adipiscing elit, sed do eiusmod tempor</p><a>View Details</a></div>
</article>

<div class="abs btn-fill">View All</div>

<h2 class="abs section-title heading" style="top:3015px">Gallery</h2>
<div class="abs gallery-item" style="left:89px" role="img" aria-label="Broccoli bake in a white dish" style="left:89px"></div>
<div class="abs gallery-item" style="left:89px;background:linear-gradient(135deg,#f4f2ea,#d6c96a 50%,#6e8d3a)" role="img" aria-label="Broccoli bake in a white dish"></div>
<div class="abs gallery-item" style="left:347px;background:linear-gradient(135deg,#2a2623,#e2b46a 50%,#5a4a3a)" role="img" aria-label="Layered lasagne slices"></div>
<div class="abs gallery-item" style="left:605px;background:linear-gradient(135deg,#e8c79a,#c97a3a 50%,#6a5040)" role="img" aria-label="Spicy beef casserole"><div class="gallery-caption">Spicy beef casserole</div></div>
<div class="abs gallery-item" style="left:863px;background:linear-gradient(135deg,#8a8a8a,#e9c98a 50%,#6e6e6e)" role="img" aria-label="Vegetable quiche with tomatoes"></div>

<svg class="abs wave" style="top:3378px" width="1200" height="40"><rect width="1200" height="40" fill="url(#scallopUp)"/></svg>
<footer class="abs site-footer">
  <span class="social" style="left:481px" aria-label="Social link"></span>
  <span class="social" style="left:542px" aria-label="Social link"></span>
  <span class="social" style="left:604px" aria-label="Social link"></span>
  <span class="social" style="left:665px" aria-label="Social link"></span>
  <div class="footer-contacts">
    <svg width="13" height="13" viewBox="0 0 24 24"><path d="M6.6 10.8c1.4 2.8 3.8 5.1 6.6 6.6l2.2-2.2c.3-.3.7-.4 1-.2 1.1.4 2.3.6 3.6.6.6 0 1 .4 1 1V20c0 .6-.4 1-1 1C10.6 21 3 13.4 3 4c0-.6.4-1 1-1h3.5c.6 0 1 .4 1 1 0 1.3.2 2.5.6 3.6.1.3 0 .7-.2 1z" fill="#fff"/></svg>
    <span>02 6100 4828</span><span>|</span>
    <svg width="15" height="12" viewBox="0 0 24 18"><rect x="1" y="1" width="22" height="16" rx="2" fill="#fff"/><path d="M2 3l10 7 10-7" fill="none" stroke="#000" stroke-width="2"/></svg>
    <span>hello@savannaplate.example</span><span>|</span>
    <svg width="14" height="14" viewBox="0 0 24 24"><circle cx="12" cy="12" r="10" fill="none" stroke="#fff" stroke-width="2.5"/><path d="M2 12h20M12 2c3 3 3 17 0 20M12 2c-3 3-3 17 0 20" fill="none" stroke="#fff" stroke-width="1.5"/></svg>
    <span>www.savannaplate.example</span>
  </div>
  <nav class="footer-nav"><span>Home</span><span>About Us</span><span>Services</span><span>We Offer</span><span>Our Dishes</span><span>Our Partners</span><span>Blog</span><span>Contact Us</span></nav>
  <div class="copyright">Copyrights © 2019, The Company Name. All rights reserved.</div>
</footer>

</body>
</html>
```